Lucky Harbour Fun Casino Entertainment

Looking to update my business card and make it look more modern, stand out and eye catching.
We are are fun casino business in Australia (primarily Sydney). Blackjack and Roulette are our most popular games although we have pretty much every game available for hire that you would find in a real casino. The final design would need to be sleek and appeal to the more upmarket corporate sector.
We mainly cater for Corporate Events, Private Parties, Fundraising Events, Team Building, Poker Tournaments
I think I'd prefer the colour Black.

Target Market(s)

High-end Corporate

Industry/Entity Type

Events

Contact Information for Business Card

Rob Kendall
Director
1300 482 617
0433 728 591
info@luckyharbour.com.au
www.luckyharbour.com.au
Facebook & Instagram @luckyharbourevents (proper social icons preferred)

Colors
000000
0255a3

Requirements
Must have
• Front side:
• Logo
• Contact details
• 'Australia's #1 Fun Casino Specialists'
• Back:
• Logo
Nice to have
• Back:
• Corporate Events
• Private Parties
• Poker Tournaments
• Fundraising
• Props & Theming
• Photo Booth
• Horse Racing Events
• The Vegas Sign attached, maybe on the back of the card in the background...?

```html
<!DOCTYPE html>
<html lang="en">
<head>
<meta charset="utf-8">
<title>Lucky Harbour – Business Card</title>
<link href="https://fonts.googleapis.com/css2?family=Open+Sans:wght@400;600;700&family=Great+Vibes&display=swap" rel="stylesheet">
<style>
  :root {
    --bg: #e9e6e1;
    --ink: #1b1b1b;
    --charcoal: #2b2b2b;
    --black: #0d0d0d;
    --orange: #f29a1e;
    --yellow: #f7d51c;
    --grey-text: #555;
    --grey-line: #c9c9c9;
    --white: #ffffff;
  }
  * { box-sizing: border-box; margin: 0; padding: 0; }
  html, body { width: 1200px; height: 942px; overflow: hidden; }
  body {
    background: var(--bg);
    font-family: "Open Sans", Arial, sans-serif;
    display: flex; flex-direction: column; align-items: center; justify-content: space-evenly;
  }
  .card {
    position: relative; width: 720px; height: 412px; border-radius: 26px; overflow: hidden;
    box-shadow: 0 10px 26px rgba(0,0,0,.25);
  }

  /* Front */
  .card-front { background: var(--white); }
  .card-front .edge-stripe {
    position: absolute; top: 0; left: 0; right: 0; height: 22px;
    background: repeating-linear-gradient(135deg, #e2e2e2 0 2px, #fff 2px 5px);
  }
  .brand { display: flex; align-items: center; gap: 12px; }
  .brand-mark { width: 54px; height: 54px; border-radius: 50%; background: var(--orange); flex: none; }
  .brand-name { font-weight: 700; font-size: 34px; color: var(--charcoal); letter-spacing: .5px; white-space: nowrap; }
  .tagline { font-family: "Great Vibes", cursive; font-size: 30px; color: var(--ink); white-space: nowrap; }
  .front-brand {
    position: absolute; left: 24px; top: 76px; width: 316px;
    display: flex; flex-direction: column; align-items: center;
  }
  .front-brand .brand-mark { width: 44px; height: 44px; }
  .front-brand .brand-name { font-size: 29px; letter-spacing: 0; }
  .front-brand .tagline { margin-top: 16px; font-size: 22px; }
  .divider { position: absolute; left: 360px; top: 56px; width: 2px; height: 220px; background: linear-gradient(var(--white), var(--grey-line), var(--white)); }
  .contact { position: absolute; left: 392px; top: 58px; color: var(--grey-text); }
  .contact .name { font-weight: 700; font-size: 28px; color: var(--orange); line-height: 1.1; }
  .contact .role { font-size: 17px; color: #999; margin-top: 2px; padding-bottom: 8px; border-bottom: 2px solid var(--orange); width: 150px; }
  .contact ul { list-style: none; margin-top: 12px; font-size: 16px; line-height: 1.75; }
  .contact li { display: flex; align-items: center; gap: 8px; white-space: nowrap; }
  .contact .icon { width: 18px; height: 18px; flex: none; }
  .contact .gap { margin-left: 10px; }
  .address-band {
    position: absolute; left: 0; right: 0; bottom: 0; height: 86px;
    background: linear-gradient(#333, var(--black));
    color: var(--white); font-weight: 700; font-size: 30px;
    display: flex; align-items: center; padding-left: 44px; white-space: nowrap;
  }

  /* Back */
  .card-back { background: linear-gradient(200deg, #4a4a4a 0%, #1e1e1e 55%, var(--black) 100%); }
  .back-brand { position: absolute; left: 0; right: 0; top: 74px; display: flex; flex-direction: column; align-items: center; }
  .back-brand .brand-mark { width: 72px; height: 72px; }
  .back-brand .brand-name { color: var(--orange); font-size: 44px; }
  .back-brand .tagline { color: var(--white); font-size: 34px; margin-top: 22px; }
  .services-band {
    position: absolute; left: 0; right: 0; bottom: 0; height: 98px;
    background: linear-gradient(90deg, var(--orange), var(--yellow) 50%, var(--orange));
    color: var(--ink); font-weight: 700; font-size: 19px; text-align: center;
    display: flex; flex-direction: column; justify-content: center; line-height: 1.55;
  }
</style>
</head>
<body>

<section class="card card-front" aria-label="Business card front">
  <div class="edge-stripe"></div>
  <div class="front-brand">
    <div class="brand">
      <span class="brand-mark"></span>
      <span class="brand-name">Lucky Harbour</span>
    </div>
    <p class="tagline">Australia's #1 Fun Casino Specialists</p>
  </div>
  <div class="divider"></div>
  <div class="contact">
    <p class="name">Rob Kendall</p>
    <p class="role">Director</p>
    <ul>
      <li>
        <svg class="icon" viewBox="0 0 18 18"><circle cx="9" cy="9" r="9" fill="#f29a1e"/><path d="M6 4.5l2 2-1 1.2c.6 1.3 1.7 2.4 3 3l1.2-1 2 2-1.3 1.6C8.6 13 5 9.4 4.7 6z" fill="#fff"/></svg>
        1300 482 617
        <svg class="icon gap" viewBox="0 0 18 18"><circle cx="9" cy="9" r="9" fill="#f29a1e"/><rect x="6" y="4" width="6" height="10" rx="1.2" fill="#fff"/></svg>
        0433 728 591
      </li>
      <li>
        <svg class="icon" viewBox="0 0 18 18"><circle cx="9" cy="9" r="9" fill="#f29a1e"/><rect x="4.5" y="5.5" width="9" height="7" fill="#fff"/><path d="M4.5 5.5L9 9.5l4.5-4" stroke="#f29a1e" fill="none"/></svg>
        info@luckyharbour.com.au
      </li>
      <li>
        <svg class="icon" viewBox="0 0 18 18"><circle cx="9" cy="9" r="9" fill="#f29a1e"/><circle cx="9" cy="9" r="4.5" stroke="#fff" stroke-width="1.4" fill="none"/><path d="M4.5 9h9M9 4.5v9" stroke="#fff" stroke-width="1.2"/></svg>
        www.luckyharbour.com.au
      </li>
      <li>
        <svg class="icon" viewBox="0 0 18 18"><circle cx="9" cy="9" r="9" fill="#f29a1e"/></svg>
        @luckyharbourevents
      </li>
      <li>
        <svg class="icon" viewBox="0 0 18 18"><circle cx="9" cy="9" r="9" fill="#f29a1e"/></svg>
        @luckyharbourevents
      </li>
    </ul>
  </div>
  <div class="address-band">7/48 Harbourview Road, Glenbrook 2773</div>
</section>

<section class="card card-back" aria-label="Business card back">
  <div class="back-brand">
    <div class="brand">
      <span class="brand-mark"></span>
      <span class="brand-name">Lucky Harbour</span>
    </div>
    <p class="tagline">Australia's #1 Fun Casino Specialists</p>
  </div>
  <div class="services-band">
    <p>Corporate Events | Private Parties | Poker Tournaments</p>
    <p>Fundraising | Props &amp; Theming | Photo Booth | Horse Racing Events</p>
  </div>
</section>

</body>
</html>
```